Indy Film Production Company/Studio

We need a business card designed from an existing logo. We are a digital studio/production company that caters to creating genre entertainment, like Action, Horror, and martial arts. The card along with the logo will be used to Brand the company from letter heads to banners. The design will also be used for postcards and Brochures. It should be professional and masculine.
Updates

Thank you to all the designers who have participated. I'm narrowing down who it will be. Thank you again.

Target Market(s)

Investors, Networks, Producers, and actors

Industry/Entity Type

Film Production

Contact Information for Business Card

Teodoro Valbuena
Producer/Writer/Director
www.kestrelpicturehouse.example

Requirements
Must have
• Website address, Facebook icon and Twitter icon possibly in the back of the card.
Nice to have
• Logline of Company: Follow The Action.

```html
<!DOCTYPE html>
<html lang="en">
<head>
<meta charset="utf-8">
<title>Kestrel Picture House – Business Card</title>
<link href="https://fonts.googleapis.com/css2?family=Fira+Sans+Condensed:wght@500&family=Roboto:wght@400;700&display=swap" rel="stylesheet">
<style>
  :root {
    --backdrop: #a8a6a6;
    --card-dark: #2e2a29;
    --card-light: #f1f1f0;
    --brand-red: #c9302b;
    --ink: #2a2a2a;
    --swoosh: #231f1f;
    --white: #ffffff;
  }
  * { margin: 0; padding: 0; box-sizing: border-box; }
  html, body {
    width: 1200px; height: 1200px; overflow: hidden;
    background: var(--backdrop);
    font-family: "Roboto", Arial, sans-serif;
  }
  .canvas { position: relative; width: 1200px; height: 1200px; }
  .card {
    position: absolute; width: 712px; height: 420px; overflow: hidden;
  }
  .card--front { left: 238px; top: 117px; background: var(--card-dark); }
  .card--back { left: 230px; top: 643px; background: var(--card-light); }

  .brand-name {
    color: var(--brand-red);
    font-family: "Roboto", Arial, sans-serif;
    font-weight: 700;
    letter-spacing: 1px;
    white-space: nowrap;
  }
  .card--front .brand-name {
    position: absolute; left: 0; right: 0; top: 188px;
    text-align: center; font-size: 38px;
  }
  .card--back .brand-name {
    position: absolute; left: 55px; top: 178px; font-size: 27px;
  }

  .wave { position: absolute; inset: 0; width: 712px; height: 420px; }

  .person {
    position: absolute; right: 32px; top: 40px; text-align: right; color: var(--white);
  }
  .person__name {
    font-family: "Fira Sans Condensed", Arial, sans-serif;
    font-weight: 500; font-size: 27px; line-height: 1.2;
  }
  .person__title { font-size: 16px; margin-top: 8px; letter-spacing: 0.3px; }

  .contacts {
    position: absolute; left: 54px; top: 296px; list-style: none;
    color: var(--ink); font-size: 18px;
  }
  .contacts li { display: flex; align-items: center; height: 28.5px; }
  .contacts svg { width: 17px; height: 17px; margin-right: 17px; fill: var(--brand-red); }

  .address {
    position: absolute; left: 455px; top: 326px;
    color: var(--ink); font-size: 18px; line-height: 29px;
  }
</style>
</head>
<body>
<main class="canvas">
  <section class="card card--front">
    <p class="brand-name">KESTREL PICTURE HOUSE</p>
  </section>

  <section class="card card--back">
    <svg class="wave" viewBox="0 0 712 420" aria-hidden="true">
      <path fill="var(--brand-red)" d="M0 0H712V200C600 190 520 140 430 85C340 35 200 20 0 58Z"/>
      <path fill="var(--swoosh)" d="M0 60C200 22 340 37 430 87C520 142 600 192 712 202V214C600 206 520 162 430 112C330 58 190 45 0 82Z"/>
    </svg>

    <div class="person">
      <p class="person__name">Your Good Name</p>
      <p class="person__title">Managing Director</p>
    </div>

    <p class="brand-name">KESTREL PICTURE HOUSE</p>

    <ul class="contacts">
      <li>
        <svg viewBox="0 0 24 24" aria-hidden="true"><path d="M3 9c0-3 4-5 9-5s9 2 9 5v2h-5V9H8v2H3z"/><path d="M6 12h12l2 8H4z"/></svg>
        +00 111 222 3333
      </li>
      <li>
        <svg viewBox="0 0 24 24" aria-hidden="true"><path d="M2 5h20v14H2z" /><path d="M2 5l10 8 10-8" fill="none" stroke="var(--card-light)" stroke-width="2"/></svg>
        yourname@yourwebsite.com
      </li>
      <li>
        <svg viewBox="0 0 24 24" aria-hidden="true"><circle cx="12" cy="12" r="10"/><path d="M2 12h20M12 2c-4 5-4 15 0 20M12 2c4 5 4 15 0 20" fill="none" stroke="var(--card-light)" stroke-width="1.6"/></svg>
        www.yourwebsite.com
      </li>
    </ul>

    <p class="address">Your Long Commercial or<br>business address in 2 line</p>
  </section>
</main>
</body>
</html>
```